A multi-page brochure that explains our firm ,KVL Wealth Management

We have a current brochure attached but it is a compilation of several items combined into one. We would like this to have the same content but be one complete theme. We are a financial planning form so it needs to have a level of professionalism but also a comfortable approach for clients and showing that was have a lot of resources and experience. We cater mostly to the 55-60+ age community.

We need the front page picture changed. lake themed would be great, like our website www.TheMoskaHouse.com
Just to be clear we use KVL Wealth Management now as our company name. Parent company name is The Moska House LLC. I attached the current mock brochure and our new logos.
Our logo colors are:
KVL WM Logo Colors:

Blue:
HEX: #0f75bc
RGB: rgba(15,117,188,255)

Grey:
HEX: #6d6e71
RGB: rgba(109,110,113,255)

Target Market(s)

High-level individuals that are looking for financial guidance who are 40 years old and up

Industry/Entity Type

Wealth Management

Requirements
Must have
• Clean and crisp
Nice to have
• https://www.bramblestoneplanners.com/wealth-management-brochure , this is a sample we like

```html
<!DOCTYPE html>
<html lang="en">
<head>
<meta charset="utf-8">
<title>KVL Wealth Management – Brochure Spread</title>
<link rel="stylesheet" href="https://fonts.googleapis.com/css2?family=Archivo:wght@400;500;600;700&display=swap">
<style>
  :root{
    --brand-blue:#0f75bc;
    --brand-deep:#0b4f8f;
    --brand-grey:#6d6e71;
    --ink:#1d1f24;
    --body:#3c3f45;
    --panel:#f1f2f3;
    --panel-line:#e1e3e6;
    --stage:#d9d9d9;
    --white:#ffffff;
  }
  *{box-sizing:border-box;margin:0;padding:0}
  html,body{width:1200px;height:1200px;overflow:hidden;background:var(--stage);font-family:"Archivo",Arial,sans-serif;color:var(--body)}
  .spread{position:absolute;left:180px;top:300px;width:840px;height:600px;display:flex;box-shadow:0 8px 24px rgba(0,0,0,.18)}
  .page{position:relative;width:420px;height:600px;background:var(--white);overflow:hidden}
  .page--left{border-right:1px solid #e4e4e4}

  .section-tag{position:absolute;display:flex;align-items:center;gap:6px;font-size:8px;color:var(--ink)}
  .section-tag::before{content:"";width:6px;height:6px;background:var(--ink)}
  .section-tag__rule{height:2px;width:150px;background:linear-gradient(90deg,var(--brand-blue),rgba(15,117,188,0))}
  .section-tag--light{color:var(--white)}
  .section-tag--light::before{background:var(--white)}
  .section-tag--light .section-tag__rule{background:linear-gradient(90deg,#fff,rgba(255,255,255,.4));width:280px}

  .deco{position:absolute;left:0;top:0}

  .headline{position:absolute;left:26px;top:112px;line-height:1.05}
  .headline__accent{display:block;font-size:25px;font-weight:700;color:var(--brand-blue)}
  .headline__rest{display:block;font-size:22px;font-weight:500;color:var(--ink)}
  .lead{position:absolute;left:26px;top:178px;width:370px;font-size:10.5px;line-height:1.6;color:var(--ink)}

  .photo{position:absolute}
  .photo--team{left:0;top:0;width:420px;height:600px}

  .footer{position:absolute;left:22px;bottom:14px;width:380px}
  .footer__brand{font-size:11px;font-weight:600;margin-bottom:4px}
  .footer__legal{font-size:5.5px;line-height:1.4}
  .footer--dark{color:var(--white)}
  .footer--light .footer__brand{color:var(--brand-blue)}
  .footer--light{border-top:1px solid var(--panel-line);padding-top:4px;bottom:10px}
  .footer--light .footer__brand{position:absolute;top:-18px}
  .footer--light .footer__legal{color:var(--brand-grey)}

  .firm-title{position:absolute;left:20px;top:150px;font-size:22px;font-weight:500;color:var(--ink)}
  .firm-title b{color:var(--brand-blue);font-weight:700}
  .firm-copy{position:absolute;left:20px;width:300px;font-size:9.5px;line-height:1.35;color:var(--ink)}
  .firm-copy--intro{top:180px}
  .firm-copy--guide{top:212px;width:330px}
  .firm-copy--closing{top:482px;width:385px;line-height:1.4}

  .principles{position:absolute;left:20px;top:248px;width:268px;display:flex;flex-direction:column;gap:8px}
  .principle{background:var(--panel);border:1px solid var(--panel-line);padding:9px 12px 10px}
  .principle__name{display:flex;align-items:center;gap:6px;font-size:10px;font-weight:500;color:var(--ink);margin-bottom:5px}
  .principle__name svg{width:12px;height:12px}
  .principle__text{font-size:7.6px;line-height:1.5;color:var(--body)}
  .principle--active{background:var(--brand-blue);border-color:var(--brand-blue)}
  .principle--active .principle__name,.principle--active .principle__text{color:var(--white)}

  .locations{position:absolute;left:302px;top:248px;width:104px}
  .location{margin-bottom:10px;text-align:center}
  .location__photo{width:104px;height:86px}
  .location__name{font-size:8px;color:var(--ink);margin-top:6px}
</style>
</head>
<body>
<main class="spread">

  <!-- Left page -->
  <section class="page page--left">
    <svg class="photo photo--team" viewBox="0 0 420 600" role="img" aria-label="Photo of a small group of clients seated in a bright meeting room listening to an advisor">
      <defs>
        <linearGradient id="teamTone" x1="0" y1="0" x2="1" y2="1">
          <stop offset="0" stop-color="#c9ccd0"/>
          <stop offset=".45" stop-color="#8b8f8f"/>
          <stop offset="1" stop-color="#3d3f44"/>
        </linearGradient>
      </defs>
      <path d="M0 380 C110 350 190 420 300 430 C360 435 400 410 420 395 L420 600 L0 600Z" fill="url(#teamTone)"/>
    </svg>

    <svg class="deco" width="420" height="600" viewBox="0 0 420 600" aria-hidden="true">
      <path d="M250 0 C300 20 360 30 420 10 L420 0Z" fill="var(--brand-grey)"/>
      <path d="M270 0 C320 40 380 45 420 30 L420 0Z" fill="var(--brand-blue)"/>
      <path d="M320 0 C350 18 390 18 420 8 L420 0Z" fill="var(--brand-deep)"/>
      <path d="M0 355 C80 330 150 370 210 395" stroke="var(--brand-grey)" stroke-width="14" fill="none"/>
      <path d="M0 378 C110 352 190 420 300 428 C360 433 400 408 420 394" stroke="var(--brand-blue)" stroke-width="6" fill="none"/>
      <path d="M200 410 C270 440 350 440 420 380" stroke="var(--brand-deep)" stroke-width="3" fill="none"/>
    </svg>

    <div class="section-tag" style="left:26px;top:74px">Wealth Management <span class="section-tag__rule"></span></div>

    <h1 class="headline">
      <span class="headline__accent">Partner</span>
      <span class="headline__rest">with a Specialist</span>
    </h1>
    <p class="lead">Understanding your unique needs and vision for the future is the starting point for our relationship. Together, we'll assess where you are financially and where you want to be. Next, we'll create a comprehensive wealth management plan that addresses your immediate and long-term goals. What about the unpredictable? We'll plan for the changes that may be ahead, too.</p>

    <footer class="footer footer--dark">
      <div class="footer__brand">KVL Wealth Management</div>
      <p class="footer__legal">Securities and advisory services offered through Lakeshore Financial Network, Member NFSA/ICPS, a Registered Investment Adviser. Fixed insurance products and services offered through Harbor Insurance Agency or The Moska House.</p>
    </footer>
  </section>

  <!-- Right page -->
  <section class="page page--right">
    <svg class="deco" width="420" height="600" viewBox="0 0 420 600">
      <defs>
        <linearGradient id="officeTone" x1="0" y1="0" x2="1" y2="0">
          <stop offset="0" stop-color="#6f8a6a"/>
          <stop offset=".5" stop-color="#a9b3ad"/>
          <stop offset="1" stop-color="#8e979d"/>
        </linearGradient>
      </defs>
      <rect width="420" height="150" fill="url(#officeTone)" role="img" aria-label="Photo of an open-plan office with hanging plants and workstations"/>
      <path d="M0 150 L0 118 C80 85 180 80 250 115 C300 140 360 120 420 110 L420 180 L0 180Z" fill="var(--white)"/>
      <path d="M270 140 C320 160 370 150 420 110 L420 200 C400 190 360 170 300 150Z" fill="var(--brand-blue)"/>
      <path d="M262 128 C320 150 370 138 420 100" stroke="var(--brand-blue)" stroke-width="2" fill="none"/>
    </svg>

    <div class="section-tag section-tag--light" style="left:28px;top:17px">Wealth Management <span class="section-tag__rule"></span></div>

    <h2 class="firm-title"><b>Our</b> Firm</h2>
    <p class="firm-copy firm-copy--intro">The Moska House LLC, established in 1987, is an independent, full-service, financial consulting firm.</p>
    <p class="firm-copy firm-copy--guide">As we search the marketplace for innovative, strategic solutions, The Moska House is guided by the following principles:</p>

    <div class="principles">
      <article class="principle">
        <h3 class="principle__name"><svg viewBox="0 0 12 12" aria-hidden="true"><rect x="1" y="3" width="10" height="7.5" rx="1" fill="none" stroke="var(--brand-blue)" stroke-width="1.2"/><path d="M4 3V1.8h4V3M1 6h10" stroke="var(--brand-blue)" stroke-width="1.2" fill="none"/></svg>Service</h3>
        <p class="principle__text">We seek to anticipate your needs and exceed your expectations in every aspect of our partnership.</p>
      </article>
      <article class="principle principle--active">
        <h3 class="principle__name"><svg viewBox="0 0 12 12" aria-hidden="true"><path d="M6 1L11 3.5 6 6 1 3.5Z M1 6l5 2.5L11 6 M1 8.5 6 11l5-2.5" stroke="#fff" stroke-width="1.1" fill="none" stroke-linejoin="round"/></svg>Planning</h3>
        <p class="principle__text">We collaborate with you by listening, asking questions, educating and helping you make informed decisions to skillfully implement appropriate, effective financial strategies.</p>
      </article>
      <article class="principle">
        <h3 class="principle__name"><svg viewBox="0 0 12 12" aria-hidden="true"><rect x="1" y="3" width="10" height="7.5" rx="1" fill="none" stroke="var(--brand-blue)" stroke-width="1.2"/><path d="M4 3V1.8h4V3M1 6h10" stroke="var(--brand-blue)" stroke-width="1.2" fill="none"/></svg>Integrity</h3>
        <p class="principle__text">We build long-term client relationships and are proud of the integrity and sensitivity we exhibit when working with all our clients.</p>
      </article>
    </div>

    <div class="locations">
      <figure class="location">
        <svg class="location__photo" viewBox="0 0 104 86" role="img" aria-label="Photo of the brick office building at the Minneapolis location"><defs><linearGradient id="mplsTone" x1="0" y1="0" x2="0" y2="1"><stop offset="0" stop-color="#4f86c9"/><stop offset=".5" stop-color="#9a6f5c"/><stop offset="1" stop-color="#6c7b5a"/></linearGradient></defs><rect width="104" height="86" fill="url(#mplsTone)"/></svg>
        <figcaption class="location__name">Minneapolis Location</figcaption>
      </figure>
      <figure class="location">
        <svg class="location__photo" viewBox="0 0 104 86" role="img" aria-label="Photo of the glass office tower at the San Francisco location"><defs><linearGradient id="sfTone" x1="0" y1="0" x2="1" y2="1"><stop offset="0" stop-color="#2f6fc0"/><stop offset=".6" stop-color="#a8c6e6"/><stop offset="1" stop-color="#dfe6ee"/></linearGradient></defs><rect width="104" height="86" fill="url(#sfTone)"/></svg>
        <figcaption class="location__name">San Francisco Location</figcaption>
      </figure>
    </div>

    <p class="firm-copy firm-copy--closing">The Moska House has created an environment of objectivity and independence in which to provide independent guidance and access to the widest variety of fiscal tools to support your financial goals. Our work complements the services of your existing advisors, including CPAs and attorneys.* The degree and sophistication of the plan varies according to your circumstances.</p>

    <footer class="footer footer--light">
      <div class="footer__brand">KVL Wealth Management</div>
      <p class="footer__legal">Securities and advisory services offered through Lakeshore Financial Network, Member NFSA/ICPS, a Registered Investment Adviser. Fixed insurance products and services offered through Harbor Insurance Agency or The Moska House.</p>
    </footer>
  </section>

</main>
</body>
</html>
```